Team email banner for internal communications

We need a team email banner/header that will be applied to all internal communications from our department to other functions. The graphic should be optimized for Outlook and be landscape in layout. We have 5 different silo within our team and will need so will either need have a blank space to denote each team or have change in colors/graphics to denote each team (see current headers attached to job description). We are looking for a banner that combines our team logo (attached) with our team name, Commercial Learning & Development. The theme should be L&D and pharmaceutical in nature.
Updates

Need extra days to review

Logo Text

The text in the banner should be Commercial Learning & Development with the team logo (attached).

```html
<!DOCTYPE html>
<html lang="en">
<head>
<meta charset="utf-8">
<title>Commercial Learning &amp; Development – Team Email Banners</title>
<link href="https://fonts.googleapis.com/css2?family=Montserrat:ital,wght@0,500;0,700;1,600&display=swap" rel="stylesheet">
<style>
  :root {
    --ink: #231f20;
    --paper: #ffffff;
    --brand-red: #d92b1f;
    --hem: #d92b1f;
    --tumor: #4a2350;
    --lead: #d92b1f;
    --access: #0b63a0;
    --ops: #d9962a;
    --dots-warm: #d4803c;
  }
  html, body {
    margin: 0;
    width: 820px;
    height: 1200px;
    overflow: hidden;
    background: var(--paper);
    font-family: "Montserrat", Arial, sans-serif;
  }
  .banner-stack {
    position: absolute;
    left: 109px;
    top: 68px;
    width: 602px;
    display: flex;
    flex-direction: column;
    gap: 15px;
  }
  .banner {
    display: block;
    width: 602px;
    height: 201px;
    background: var(--paper);
    box-shadow: 0 1px 4px rgba(0,0,0,.35);
  }
  .hematology { --accent: var(--hem); --dots: var(--hem); --photo-a: #f6c4c0; --photo-b: #c8141c; }
  .solid-tumor { --accent: var(--tumor); --dots: var(--tumor); --photo-a: #1a1418; --photo-b: #b5627f; }
  .leadership { --accent: var(--lead); --dots: var(--lead); --photo-a: #cfe3f2; --photo-b: #d9a48a; }
  .market-access { --accent: var(--access); --dots: var(--dots-warm); --photo-a: #9cc4e8; --photo-b: #1d3f6b; }
  .operations { --accent: var(--ops); --dots: var(--dots-warm); --photo-a: #f7dc6a; --photo-b: #5a3a1c; }

  .accent { fill: var(--accent); }
  .dot { fill: var(--dots); }
  .ink { fill: var(--ink); }
  .paper { fill: var(--paper); }
  .stop-a { stop-color: var(--photo-a); }
  .stop-b { stop-color: var(--photo-b); }
  .edge { stroke: var(--ink); stroke-width: 4; fill: none; }
  .rule { stroke: var(--ink); stroke-width: 3; }
  .logo-mark { fill: var(--brand-red); }
  .team-name { font-family: "Montserrat", Arial, sans-serif; font-weight: 500; fill: var(--ink); }
  .team-name-main { font-size: 56px; }
  .team-name-sub { font-size: 17px; }
  .silo-title { font-family: "Montserrat", Arial, sans-serif; font-style: italic; font-weight: 600; font-size: 40px; fill: var(--accent); }
  .company-name { font-family: "Montserrat", Arial, sans-serif; font-weight: 700; font-size: 30px; fill: var(--paper); }
  .company-square { fill: var(--brand-red); }
</style>
</head>
<body>
<main class="banner-stack">

  <!-- Banner template repeated per silo -->
  <svg class="banner hematology" viewBox="0 0 1166 389" preserveAspectRatio="none">
    <defs><linearGradient id="photo-hematology" x1="0" y1="0" x2="1" y2="1"><stop offset="0" class="stop-a"/><stop offset="1" class="stop-b"/></linearGradient></defs>
    <polygon points="129,0 559,0 459,389 39,389" fill="url(#photo-hematology)" role="img" aria-label="Photo of red blood cells flowing through a vessel"/>
    <line class="edge" x1="129" y1="0" x2="39" y2="389"/><line class="edge" x1="559" y1="0" x2="459" y2="389"/>
    <polygon class="accent" points="0,0 89,0 59,117 0,117"/>
    <polygon class="accent" points="59,195 119,195 79,350 19,350"/>
    <polygon class="accent" points="509,39 576,39 539,195 479,195"/>
    <polygon class="accent" points="539,273 599,273 569,389 509,389"/>
    <polygon class="accent" points="824,27 1166,27 1166,79 835,79"/>
    <rect class="ink" x="979" y="0" width="187" height="27"/>
    <polygon class="paper" points="1000,0 1010,0 1016,27 1006,27"/><polygon class="paper" points="1025,0 1035,0 1041,27 1031,27"/><polygon class="paper" points="1050,0 1062,0 1068,27 1056,27"/>
    <g><circle class="dot" cx="630" cy="38" r="4"/><circle class="dot" cx="648" cy="38" r="4"/><circle class="dot" cx="666" cy="38" r="4"/><circle class="dot" cx="684" cy="38" r="4"/><circle class="dot" cx="630" cy="55" r="4"/><circle class="dot" cx="648" cy="55" r="4"/><circle class="dot" cx="666" cy="55" r="4"/><circle class="dot" cx="684" cy="55" r="4"/><circle class="dot" cx="630" cy="72" r="4"/><circle class="dot" cx="648" cy="72" r="4"/><circle class="dot" cx="666" cy="72" r="4"/><circle class="dot" cx="684" cy="72" r="4"/></g>
    <circle class="logo-mark" cx="672" cy="170" r="38"/>
    <text class="team-name team-name-main" x="1116" y="204" text-anchor="end">COMMERCIAL</text>
    <line class="rule" x1="714" y1="217" x2="860" y2="217"/>
    <text class="team-name team-name-sub" x="1116" y="223" text-anchor="end">LEARNING &amp; DEVELOPMENT</text>
    <text class="silo-title" x="1118" y="268" text-anchor="end">Hematology</text>
    <polygon class="ink" points="864,337 874,337 862,389 852,389"/><polygon class="ink" points="880,337 890,337 878,389 868,389"/>
    <polygon class="ink" points="906,337 1166,337 1166,389 892,389"/>
    <rect class="company-square" x="941" y="348" width="30" height="30"/>
    <text class="company-name" x="1116" y="374" text-anchor="end">Norvale</text>
  </svg>

  <svg class="banner solid-tumor" viewBox="0 0 1166 389" preserveAspectRatio="none">
    <defs><radialGradient id="photo-tumor" cx="0.6" cy="0.4" r="0.7"><stop offset="0" class="stop-b"/><stop offset="1" class="stop-a"/></radialGradient></defs>
    <polygon points="129,0 559,0 459,389 39,389" fill="url(#photo-tumor)" role="img" aria-label="Microscope image of tumour cells"/>
    <line class="edge" x1="129" y1="0" x2="39" y2="389"/><line class="edge" x1="559" y1="0" x2="459" y2="389"/>
    <polygon class="accent" points="0,0 89,0 59,117 0,117"/>
    <polygon class="accent" points="59,195 119,195 79,350 19,350"/>
    <polygon class="accent" points="509,39 576,39 539,195 479,195"/>
    <polygon class="accent" points="539,273 599,273 569,389 509,389"/>
    <polygon class="accent" points="824,27 1166,27 1166,79 835,79"/>
    <rect class="ink" x="979" y="0" width="187" height="27"/>
    <polygon class="paper" points="1000,0 1010,0 1016,27 1006,27"/><polygon class="paper" points="1025,0 1035,0 1041,27 1031,27"/><polygon class="paper" points="1050,0 1062,0 1068,27 1056,27"/>
    <g><circle class="dot" cx="630" cy="38" r="4"/><circle class="dot" cx="648" cy="38" r="4"/><circle class="dot" cx="666" cy="38" r="4"/><circle class="dot" cx="684" cy="38" r="4"/><circle class="dot" cx="630" cy="55" r="4"/><circle class="dot" cx="648" cy="55" r="4"/><circle class="dot" cx="666" cy="55" r="4"/><circle class="dot" cx="684" cy="55" r="4"/><circle class="dot" cx="630" cy="72" r="4"/><circle class="dot" cx="648" cy="72" r="4"/><circle class="dot" cx="666" cy="72" r="4"/><circle class="dot" cx="684" cy="72" r="4"/></g>
    <circle class="logo-mark" cx="672" cy="170" r="38"/>
    <text class="team-name team-name-main" x="1116" y="204" text-anchor="end">COMMERCIAL</text>
    <line class="rule" x1="714" y1="217" x2="860" y2="217"/>
    <text class="team-name team-name-sub" x="1116" y="223" text-anchor="end">LEARNING &amp; DEVELOPMENT</text>
    <text class="silo-title" x="1116" y="268" text-anchor="end">Solid Tumor</text>
    <polygon class="ink" points="864,337 874,337 862,389 852,389"/><polygon class="ink" points="880,337 890,337 878,389 868,389"/>
    <polygon class="ink" points="906,337 1166,337 1166,389 892,389"/>
    <rect class="company-square" x="941" y="348" width="30" height="30"/>
    <text class="company-name" x="1116" y="374" text-anchor="end">Norvale</text>
  </svg>

  <svg class="banner leadership" viewBox="0 0 1166 389" preserveAspectRatio="none">
    <defs><linearGradient id="photo-leadership" x1="1" y1="0" x2="0" y2="1"><stop offset="0" class="stop-a"/><stop offset="1" class="stop-b"/></linearGradient></defs>
    <polygon points="129,0 559,0 459,389 39,389" fill="url(#photo-leadership)" role="img" aria-label="Photo of team members joining hands"/>
    <line class="edge" x1="129" y1="0" x2="39" y2="389"/><line class="edge" x1="559" y1="0" x2="459" y2="389"/>
    <polygon class="accent" points="0,0 89,0 59,117 0,117"/>
    <polygon class="accent" points="59,195 119,195 79,350 19,350"/>
    <polygon class="accent" points="509,39 576,39 539,195 479,195"/>
    <polygon class="accent" points="539,273 599,273 569,389 509,389"/>
    <polygon class="accent" points="824,27 1166,27 1166,79 835,79"/>
    <rect class="ink" x="979" y="0" width="187" height="27"/>
    <polygon class="paper" points="1000,0 1010,0 1016,27 1006,27"/><polygon class="paper" points="1025,0 1035,0 1041,27 1031,27"/><polygon class="paper" points="1050,0 1062,0 1068,27 1056,27"/>
    <g><circle class="dot" cx="630" cy="38" r="4"/><circle class="dot" cx="648" cy="38" r="4"/><circle class="dot" cx="666" cy="38" r="4"/><circle class="dot" cx="684" cy="38" r="4"/><circle class="dot" cx="630" cy="55" r="4"/><circle class="dot" cx="648" cy="55" r="4"/><circle class="dot" cx="666" cy="55" r="4"/><circle class="dot" cx="684" cy="55" r="4"/><circle class="dot" cx="630" cy="72" r="4"/><circle class="dot" cx="648" cy="72" r="4"/><circle class="dot" cx="666" cy="72" r="4"/><circle class="dot" cx="684" cy="72" r="4"/></g>
    <circle class="logo-mark" cx="672" cy="170" r="38"/>
    <text class="team-name team-name-main" x="1116" y="204" text-anchor="end">COMMERCIAL</text>
    <line class="rule" x1="714" y1="217" x2="860" y2="217"/>
    <text class="team-name team-name-sub" x="1116" y="223" text-anchor="end">LEARNING &amp; DEVELOPMENT</text>
    <text class="silo-title" x="1116" y="266" text-anchor="end">Leadership Development</text>
    <polygon class="ink" points="864,337 874,337 862,389 852,389"/><polygon class="ink" points="880,337 890,337 878,389 868,389"/>
    <polygon class="ink" points="906,337 1166,337 1166,389 892,389"/>
    <rect class="company-square" x="941" y="348" width="30" height="30"/>
    <text class="company-name" x="1116" y="374" text-anchor="end">Norvale</text>
  </svg>

  <svg class="banner market-access" viewBox="0 0 1166 389" preserveAspectRatio="none">
    <defs><linearGradient id="photo-access" x1="0" y1="0" x2="1" y2="1"><stop offset="0" class="stop-a"/><stop offset="1" class="stop-b"/></linearGradient></defs>
    <polygon points="129,0 559,0 459,389 39,389" fill="url(#photo-access)" role="img" aria-label="Photo of a business handshake in front of an office building"/>
    <line class="edge" x1="129" y1="0" x2="39" y2="389"/><line class="edge" x1="559" y1="0" x2="459" y2="389"/>
    <polygon class="accent" points="0,0 89,0 59,117 0,117"/>
    <polygon class="accent" points="59,195 119,195 79,350 19,350"/>
    <polygon class="accent" points="509,39 576,39 539,195 479,195"/>
    <polygon class="accent" points="539,273 599,273 569,389 509,389"/>
    <polygon class="accent" points="824,27 1166,27 1166,79 835,79"/>
    <rect class="ink" x="979" y="0" width="187" height="27"/>
    <polygon class="paper" points="1000,0 1010,0 1016,27 1006,27"/><polygon class="paper" points="1025,0 1035,0 1041,27 1031,27"/><polygon class="paper" points="1050,0 1062,0 1068,27 1056,27"/>
    <g><circle class="dot" cx="630" cy="38" r="4"/><circle class="dot" cx="648" cy="38" r="4"/><circle class="dot" cx="666" cy="38" r="4"/><circle class="dot" cx="684" cy="38" r="4"/><circle class="dot" cx="630" cy="55" r="4"/><circle class="dot" cx="648" cy="55" r="4"/><circle class="dot" cx="666" cy="55" r="4"/><circle class="dot" cx="684" cy="55" r="4"/><circle class="dot" cx="630" cy="72" r="4"/><circle class="dot" cx="648" cy="72" r="4"/><circle class="dot" cx="666" cy="72" r="4"/><circle class="dot" cx="684" cy="72" r="4"/></g>
    <circle class="logo-mark" cx="672" cy="170" r="38"/>
    <text class="team-name team-name-main" x="1116" y="204" text-anchor="end">COMMERCIAL</text>
    <line class="rule" x1="714" y1="217" x2="860" y2="217"/>
    <text class="team-name team-name-sub" x="1116" y="223" text-anchor="end">LEARNING &amp; DEVELOPMENT</text>
    <text class="silo-title" x="1116" y="266" text-anchor="end">Market Access</text>
    <polygon class="ink" points="864,337 874,337 862,389 852,389"/><polygon class="ink" points="880,337 890,337 878,389 868,389"/>
    <polygon class="ink" points="906,337 1166,337 1166,389 892,389"/>
    <rect class="company-square" x="941" y="348" width="30" height="30"/>
    <text class="company-name" x="1116" y="374" text-anchor="end">Norvale</text>
  </svg>

  <svg class="banner operations" viewBox="0 0 1166 389" preserveAspectRatio="none">
    <defs><linearGradient id="photo-operations" x1="0" y1="0" x2="0" y2="1"><stop offset="0" class="stop-a"/><stop offset="1" class="stop-b"/></linearGradient></defs>
    <polygon points="129,0 559,0 459,389 39,389" fill="url(#photo-operations)" role="img" aria-label="Photo of a silhouette climbing rising steps at sunset"/>
    <line class="edge" x1="129" y1="0" x2="39" y2="389"/><line class="edge" x1="559" y1="0" x2="459" y2="389"/>
    <polygon class="accent" points="0,0 89,0 59,117 0,117"/>
    <polygon class="accent" points="59,195 119,195 79,350 19,350"/>
    <polygon class="accent" points="509,39 576,39 539,195 479,195"/>
    <polygon class="accent" points="539,273 599,273 569,389 509,389"/>
    <polygon class="accent" points="824,27 1166,27 1166,79 835,79"/>
    <rect class="ink" x="979" y="0" width="187" height="27"/>
    <polygon class="paper" points="1000,0 1010,0 1016,27 1006,27"/><polygon class="paper" points="1025,0 1035,0 1041,27 1031,27"/><polygon class="paper" points="1050,0 1062,0 1068,27 1056,27"/>
    <g><circle class="dot" cx="630" cy="38" r="4"/><circle class="dot" cx="648" cy="38" r="4"/><circle class="dot" cx="666" cy="38" r="4"/><circle class="dot" cx="684" cy="38" r="4"/><circle class="dot" cx="630" cy="55" r="4"/><circle class="dot" cx="648" cy="55" r="4"/><circle class="dot" cx="666" cy="55" r="4"/><circle class="dot" cx="684" cy="55" r="4"/><circle class="dot" cx="630" cy="72" r="4"/><circle class="dot" cx="648" cy="72" r="4"/><circle class="dot" cx="666" cy="72" r="4"/><circle class="dot" cx="684" cy="72" r="4"/></g>
    <circle class="logo-mark" cx="672" cy="170" r="38"/>
    <text class="team-name team-name-main" x="1116" y="204" text-anchor="end">COMMERCIAL</text>
    <line class="rule" x1="714" y1="217" x2="860" y2="217"/>
    <text class="team-name team-name-sub" x="1116" y="223" text-anchor="end">LEARNING &amp; DEVELOPMENT</text>
    <text class="silo-title" x="1116" y="266" text-anchor="end">Operations &amp; Capabilities</text>
    <polygon class="ink" points="864,337 874,337 862,389 852,389"/><polygon class="ink" points="880,337 890,337 878,389 868,389"/>
    <polygon class="ink" points="906,337 1166,337 1166,389 892,389"/>
    <rect class="company-square" x="941" y="348" width="30" height="30"/>
    <text class="company-name" x="1116" y="374" text-anchor="end">Norvale</text>
  </svg>

</main>
</body>
</html>
```